Structural Engineering Business Card

Brookvane Drafting does residential house plans for clients in Central Florida. Would like simple but elegant business card that is appropriate for a house plan engineering company. Prefer black business card with black/white them but open to other shades of blue. I uploaded a sample card that I came across that looked good but please come up with your own creative designs.

Contact Information for Business Card

Name, Title, Phone, Email, Address, website

```html
<!DOCTYPE html>
<html lang="en">
<head>
<meta charset="utf-8">
<title>Brookvane Drafting – Business Card</title>
<link href="https://fonts.googleapis.com/css2?family=Montserrat:wght@400;800&display=swap" rel="stylesheet">
<style>
  :root {
    --canvas: #c9c9c9;
    --card: #ffffff;
    --ink: #0d0d0d;
    --muted: #5a5a5a;
    --shadow: rgba(0,0,0,0.18);
  }
  * { margin: 0; padding: 0; box-sizing: border-box; }
  html, body {
    width: 1200px; height: 1200px; overflow: hidden;
    background: var(--canvas);
    font-family: "Montserrat", sans-serif;
  }
  .sheet {
    width: 1200px; height: 1200px;
    display: flex; flex-direction: column; align-items: center; justify-content: center;
    gap: 60px;
  }
  .card {
    position: relative;
    width: 840px; height: 480px;
    background: var(--card);
    box-shadow: 0 12px 30px var(--shadow);
  }
  .card-front .identity {
    position: absolute; left: 70px; top: 64px;
  }
  .identity .name {
    font-weight: 800; font-size: 30px; color: var(--ink); letter-spacing: 0.3px;
  }
  .identity .title {
    font-weight: 400; font-size: 24px; color: var(--muted); margin-top: 2px;
  }
  .wordmark {
    font-weight: 800; color: var(--ink); text-transform: uppercase; letter-spacing: 0.5px;
    line-height: 1.05;
  }
  .card-front .wordmark {
    position: absolute; right: 70px; top: 150px; font-size: 40px; text-align: right;
  }
  .contacts {
    position: absolute; left: 70px; top: 300px;
    list-style: none;
  }
  .contact {
    display: flex; align-items: center; gap: 14px;
    font-size: 22px; color: var(--muted); height: 38px;
  }
  .icon {
    width: 26px; height: 26px; flex: none;
  }
  .address {
    position: absolute; left: 460px; top: 372px;
    display: flex; align-items: flex-start; gap: 14px;
    font-size: 22px; color: var(--muted); line-height: 1.3;
  }
  .card-back {
    display: flex; align-items: center; justify-content: center;
  }
  .card-back .wordmark { font-size: 64px; text-align: center; }
</style>
</head>
<body>
<main class="sheet">

  <section class="card card-front">
    <div class="identity">
      <p class="name">DORIAN VECK</p>
      <p class="title">Owner</p>
    </div>

    <p class="wordmark">Brookvane<br>Drafting</p>

    <ul class="contacts">
      <li class="contact">
        <svg class="icon" viewBox="0 0 26 26" aria-hidden="true">
          <circle cx="13" cy="13" r="13" fill="var(--ink)"/>
          <path d="M9 7.5l2.2 2.6-1.3 1.6c.9 1.8 2.2 3.1 4 4l1.6-1.3 2.6 2.2-1.3 1.9c-4.6-.6-8.6-4.6-9.2-9.2z" fill="#fff"/>
        </svg>
        (555) 014-2290
      </li>
      <li class="contact">
        <svg class="icon" viewBox="0 0 26 26" aria-hidden="true">
          <circle cx="13" cy="13" r="13" fill="var(--ink)"/>
          <rect x="7" y="8.5" width="12" height="9" rx="1" fill="none" stroke="#fff" stroke-width="1.5"/>
          <path d="M7.5 9.5l5.5 4.2 5.5-4.2" fill="none" stroke="#fff" stroke-width="1.5"/>
        </svg>
        studio@brookvane.com
      </li>
      <li class="contact">
        <svg class="icon" viewBox="0 0 26 26" aria-hidden="true">
          <circle cx="13" cy="13" r="13" fill="var(--ink)"/>
          <circle cx="13" cy="13" r="6.5" fill="none" stroke="#fff" stroke-width="1.4"/>
          <ellipse cx="13" cy="13" rx="2.8" ry="6.5" fill="none" stroke="#fff" stroke-width="1.2"/>
          <path d="M6.5 13h13" stroke="#fff" stroke-width="1.2"/>
        </svg>
        www.brookvane.com
      </li>
    </ul>

    <div class="address">
      <svg class="icon" viewBox="0 0 26 26" aria-hidden="true">
        <circle cx="13" cy="13" r="13" fill="var(--ink)"/>
        <path d="M13 5.5a5 5 0 0 0-5 5c0 3.8 5 9.5 5 9.5s5-5.7 5-9.5a5 5 0 0 0-5-5z" fill="#fff"/>
        <circle cx="13" cy="10.5" r="1.9" fill="var(--ink)"/>
      </svg>
      <p>218 Larkspur Row<br>Orlando, FL 32801</p>
    </div>
  </section>

  <section class="card card-back">
    <p class="wordmark">Brookvane<br>Drafting</p>
  </section>

</main>
</body>
</html>
```